Dorrance's Anvil BBQ Sauce Needs a Label

We are looking for a rustic label that would help our product stand out on a shelf. The company name is Dorrance's Anvil. We are a new company looking to stand out on shelving with our amazing BBQ Sweet, Spicy and Rub. The label size needs to be 6.5" wide x 2.5" tall. I have taken a step in creating a label which is attached. This is just an idea for you to bring us an amazing retail ready look. On the left side of the label we need to have a 1 color flag with Made In USA. Also would need to have the address on the same side. Dorrance's Anvil BBQ Sauce, Cedar Hollow, FL 32990. The nutrition Facts are also needed. The information is correct but would need to be adjusted as to font and sizing. Image 7247 is what I have lightly put together and image 2495 is current logo on actual label. If you need any more guidance please let me know. Merles TangFire is an example of the pop we would like to see

Requirements
Must have
• Rustic Look
Nice to have
• Rustic look with a feeling similar to image 7247 that’s attached.
Should not have
• Same look as the original logo that’s on the actual label.

```html
<!DOCTYPE html>
<html lang="en">
<head>
<meta charset="utf-8">
<title>Dorrance's Anvil BBQ Sauce — Label Set</title>
<link href="https://fonts.googleapis.com/css2?family=Outfit:wght@400;500;700;800;900&display=swap" rel="stylesheet">
<style>
  :root{
    --paper:#ecdcb8;
    --paper-light:#f3e8cc;
    --ink:#3a2723;
    --ink-soft:#4a3631;
    --spicy:#c8282c;
    --sweet:#1f4f9c;
    --rub:#e0611f;
    --white:#fbf8f1;
    --plaque:#efe3c6;
  }
  *{box-sizing:border-box;margin:0;padding:0}
  html,body{width:1053px;height:1200px;overflow:hidden;background:#fff}
  body{position:relative;font-family:"Outfit",sans-serif;color:var(--ink)}

  .label{
    position:absolute;left:120px;width:798px;height:307px;overflow:hidden;
    background:
      radial-gradient(ellipse 120px 80px at 30px 20px, rgba(190,140,80,.35), transparent 70%),
      radial-gradient(ellipse 160px 70px at 760px 300px, rgba(190,140,80,.25), transparent 70%),
      radial-gradient(ellipse 90px 60px at 200px 40px, rgba(200,160,100,.25), transparent 70%),
      radial-gradient(ellipse 400px 200px at 400px 150px, var(--paper-light), var(--paper));
  }
  .label--spicy{top:87px;--accent:var(--spicy)}
  .label--sweet{top:427px;--accent:var(--sweet)}
  .label--rub{top:768px;--accent:var(--rub)}

  .info{position:absolute;left:18px;top:23px;width:180px;font-size:8.6px;line-height:10.8px}
  .info strong{font-weight:800}
  .info .storage{margin-top:11px;font-weight:800}

  .flag{position:absolute;left:18px;top:186px;width:74px;height:40px}
  .made-in{position:absolute;left:18px;top:227px;font-size:10.5px;font-weight:900;letter-spacing:.2px}
  .maker{position:absolute;left:18px;top:248px;font-size:8.6px;line-height:10.8px}
  .maker strong{font-weight:800}
  .web{position:absolute;left:18px;top:273px;font-size:8.8px;font-weight:500}

  .emblem{position:absolute;left:249px;top:22px;width:302px;height:262px}
  .emblem-art{position:absolute;inset:0;border-radius:48% 48% 50% 50% / 40% 40% 60% 60%;
    background:radial-gradient(circle at 50% 45%, var(--white) 0 38%, #c9b08c 52%, var(--ink-soft) 70%)}
  .brand-name{position:absolute;left:0;right:0;top:92px;text-align:center;
    font-weight:900;font-size:30px;line-height:32px;color:var(--ink);text-transform:uppercase;letter-spacing:.5px}
  .variant{position:absolute;left:101px;width:100px;top:226px;height:22px;line-height:22px;text-align:center;
    background:var(--plaque);border-radius:2px;font-size:14px;font-weight:900;letter-spacing:1.5px;color:var(--accent)}
  .size{position:absolute;left:493px;top:251px;font-size:15px;font-weight:800}

  .band{position:absolute;left:0;right:0;bottom:6px;height:7px;background:var(--accent)}
  .band-base{position:absolute;left:0;right:0;bottom:0;height:6px;background:var(--ink)}

  .nutrition{position:absolute;left:639px;top:14px;width:141px;height:272px;border:1px solid var(--ink);padding:3px 6px;font-size:7.4px;line-height:8.4px;overflow:hidden}
  .nutrition h2{font-size:14.5px;font-weight:900;line-height:15px;letter-spacing:.4px}
  .nf-row{display:flex;justify-content:space-between;border-bottom:.6px solid var(--ink);padding:2.4px 0 1.2px}
  .nf-row.indent{padding-left:8px}
  .nf-row.last{border-bottom:0}
  .nf-row b{font-weight:700}
  .nf-plain{display:flex;justify-content:space-between}
  .bar-thick{height:6px;background:var(--ink);margin:2px 0}
  .bar-mid{height:3px;background:var(--ink);margin:1px 0}
  .nf-small{font-size:6.2px;font-weight:700;padding:2px 0 0}
  .nf-right{text-align:right;font-size:6.2px;font-weight:700;border-bottom:.6px solid var(--ink);padding-bottom:1px}
  .nf-foot{font-size:4.6px;line-height:5px;padding-top:2px}
</style>
</head>
<body>

<section class="label label--spicy">
  <div class="info"><strong>Ingredients:</strong><br>Tomato, Chili Sauce<br>Vinegar, Worcester,<br>Sugar, Onion Lemon,<br>Honey and Spices<p class="storage">Refrigerate After Opening</p></div>
  <svg class="flag" viewBox="0 0 74 40" role="img" aria-label="One colour US flag"><g fill="var(--ink)"><rect y="0" width="74" height="3.1"/><rect y="6.2" width="74" height="3.1"/><rect y="12.4" width="74" height="3.1"/><rect y="18.6" width="74" height="3.1"/><rect y="24.8" width="74" height="3.1"/><rect y="31" width="74" height="3.1"/><rect y="37.2" width="74" height="2.8"/><rect width="30" height="21.7"/></g></svg>
  <div class="made-in">MADE IN USA</div>
  <div class="maker"><strong>Dorrance's Anvil BBQ Sauce,</strong><br>Cedar Hollow, FL 32990</div>
  <div class="web">www.dorrancesbbqsauce.com</div>
  <div class="emblem">
    <div class="emblem-art" role="img" aria-label="Rustic horseshoe emblem artwork in cream and dark brown"></div>
    <div class="brand-name">Dorrance's Anvil<br>BBQ Sauce</div>
    <div class="variant">SPICY</div>
  </div>
  <div class="size">16 oz.</div>
  <div class="nutrition">
    <h2>Nutrition Facts</h2>
    <div class="nf-plain"><span>Serving Size 1 Tbsp. (18g)</span></div>
    <div class="nf-plain"><span>Servings Per Container</span><span>25</span></div>
    <div class="bar-thick"></div>
    <div class="nf-small">Amount Per Serving</div>
    <div class="nf-row"><span><b>Calories</b> 25</span><span>Calories from Fat 0</span></div>
    <div class="bar-mid"></div>
    <div class="nf-right">% Daily Value*</div>
    <div class="nf-row"><span><b>Total Fat</b> 0g</span><b>0%</b></div>
    <div class="nf-row indent"><span>Saturated Fat 0g</span><b>0%</b></div>
    <div class="nf-row indent"><span>Trans Fat 0g</span></div>
    <div class="nf-row"><span><b>Cholesterol</b> 0mg</span><b>0%</b></div>
    <div class="nf-row"><span><b>Sodium</b> 150mg</span><b>6%</b></div>
    <div class="nf-row"><span><b>Total Carbohydrate</b> 6g</span><b>2%</b></div>
    <div class="nf-row indent"><span>Dietary Fiber 0g</span><b>0%</b></div>
    <div class="nf-row indent"><span>Sugars 6g</span></div>
    <div class="nf-row last"><span><b>Protein</b> 0.2g</span></div>
    <div class="bar-thick"></div>
    <div class="nf-row"><span>Vitamin A 1%</span><span>• Vitamin C 1%</span></div>
    <div class="nf-row"><span>Calcium 1%</span><span>• Iron 1%</span></div>
    <p class="nf-foot">*Percent Daily Values are based on a 2,000 calorie diet. Your daily values may be higher or lower depending on your calorie needs</p>
  </div>
  <div class="band"></div><div class="band-base"></div>
</section>

<section class="label label--sweet">
  <div class="info"><strong>Ingredients:</strong><br>Tomato, Chili Sauce<br>Vinegar, Worcester,<br>Sugar, Onion Lemon,<br>Honey and Spices<p class="storage">Refrigerate After Opening</p></div>
  <svg class="flag" viewBox="0 0 74 40" role="img" aria-label="One colour US flag"><g fill="var(--ink)"><rect y="0" width="74" height="3.1"/><rect y="6.2" width="74" height="3.1"/><rect y="12.4" width="74" height="3.1"/><rect y="18.6" width="74" height="3.1"/><rect y="24.8" width="74" height="3.1"/><rect y="31" width="74" height="3.1"/><rect y="37.2" width="74" height="2.8"/><rect width="30" height="21.7"/></g></svg>
  <div class="made-in">MADE IN USA</div>
  <div class="maker"><strong>Dorrance's Anvil BBQ Sauce,</strong><br>Cedar Hollow, FL 32990</div>
  <div class="web">www.dorrancesbbqsauce.com</div>
  <div class="emblem">
    <div class="emblem-art" role="img" aria-label="Rustic horseshoe emblem artwork in cream and dark brown"></div>
    <div class="brand-name">Dorrance's Anvil<br>BBQ Sauce</div>
    <div class="variant">SWEET</div>
  </div>
  <div class="size">16 oz.</div>
  <div class="nutrition">
    <h2>Nutrition Facts</h2>
    <div class="nf-plain"><span>Serving Size 1 Tbsp. (18g)</span></div>
    <div class="nf-plain"><span>Servings Per Container</span><span>25</span></div>
    <div class="bar-thick"></div>
    <div class="nf-small">Amount Per Serving</div>
    <div class="nf-row"><span><b>Calories</b> 25</span><span>Calories from Fat 0</span></div>
    <div class="bar-mid"></div>
    <div class="nf-right">% Daily Value*</div>
    <div class="nf-row"><span><b>Total Fat</b> 0g</span><b>0%</b></div>
    <div class="nf-row indent"><span>Saturated Fat 0g</span><b>0%</b></div>
    <div class="nf-row indent"><span>Trans Fat 0g</span></div>
    <div class="nf-row"><span><b>Cholesterol</b> 0mg</span><b>0%</b></div>
    <div class="nf-row"><span><b>Sodium</b> 150mg</span><b>6%</b></div>
    <div class="nf-row"><span><b>Total Carbohydrate</b> 6g</span><b>2%</b></div>
    <div class="nf-row indent"><span>Dietary Fiber 0g</span><b>0%</b></div>
    <div class="nf-row indent"><span>Sugars 6g</span></div>
    <div class="nf-row last"><span><b>Protein</b> 0.2g</span></div>
    <div class="bar-thick"></div>
    <div class="nf-row"><span>Vitamin A 1%</span><span>• Vitamin C 1%</span></div>
    <div class="nf-row"><span>Calcium 1%</span><span>• Iron 1%</span></div>
    <p class="nf-foot">*Percent Daily Values are based on a 2,000 calorie diet. Your daily values may be higher or lower depending on your calorie needs</p>
  </div>
  <div class="band"></div><div class="band-base"></div>
</section>

<section class="label label--rub">
  <div class="info"><strong>Ingredients:</strong><br>Tomato, Chili Sauce<br>Vinegar, Worcester,<br>Sugar, Onion Lemon,<br>Honey and Spices<p class="storage">Refrigerate After Opening</p></div>
  <svg class="flag" viewBox="0 0 74 40" role="img" aria-label="One colour US flag"><g fill="var(--ink)"><rect y="0" width="74" height="3.1"/><rect y="6.2" width="74" height="3.1"/><rect y="12.4" width="74" height="3.1"/><rect y="18.6" width="74" height="3.1"/><rect y="24.8" width="74" height="3.1"/><rect y="31" width="74" height="3.1"/><rect y="37.2" width="74" height="2.8"/><rect width="30" height="21.7"/></g></svg>
  <div class="made-in">MADE IN USA</div>
  <div class="maker"><strong>Dorrance's Anvil BBQ Sauce,</strong><br>Cedar Hollow, FL 32990</div>
  <div class="web">www.dorrancesbbqsauce.com</div>
  <div class="emblem">
    <div class="emblem-art" role="img" aria-label="Rustic horseshoe emblem artwork in cream and dark brown"></div>
    <div class="brand-name">Dorrance's Anvil<br>BBQ Sauce</div>
    <div class="variant">RUB</div>
  </div>
  <div class="nutrition">
    <h2>Nutrition Facts</h2>
    <div class="nf-plain"><span>Serving Size 1 Tbsp. (18g)</span></div>
    <div class="nf-plain"><span>Servings Per Container</span><span>25</span></div>
    <div class="bar-thick"></div>
    <div class="nf-small">Amount Per Serving</div>
    <div class="nf-row"><span><b>Calories</b> 25</span><span>Calories from Fat 0</span></div>
    <div class="bar-mid"></div>
    <div class="nf-right">% Daily Value*</div>
    <div class="nf-row"><span><b>Total Fat</b> 0g</span><b>0%</b></div>
    <div class="nf-row indent"><span>Saturated Fat 0g</span><b>0%</b></div>
    <div class="nf-row indent"><span>Trans Fat 0g</span></div>
    <div class="nf-row"><span><b>Cholesterol</b> 0mg</span><b>0%</b></div>
    <div class="nf-row"><span><b>Sodium</b> 150mg</span><b>6%</b></div>
    <div class="nf-row"><span><b>Total Carbohydrate</b> 6g</span><b>2%</b></div>
    <div class="nf-row indent"><span>Dietary Fiber 0g</span><b>0%</b></div>
    <div class="nf-row indent"><span>Sugars 6g</span></div>
    <div class="nf-row last"><span><b>Protein</b> 0.2g</span></div>
    <div class="bar-thick"></div>
    <div class="nf-row"><span>Vitamin A 1%</span><span>• Vitamin C 1%</span></div>
    <div class="nf-row"><span>Calcium 1%</span><span>• Iron 1%</span></div>
    <p class="nf-foot">*Percent Daily Values are based on a 2,000 calorie diet. Your daily values may be higher or lower depending on your calorie needs</p>
  </div>
  <div class="band"></div><div class="band-base"></div>
</section>

</body>
</html>
```